I want a website to be designed for our new company, it's an import and export company for variety of things.

please see the attached Logo for our company and the Images for our different sections for our busienss

Target Market(s)

multiple

Coding

Coded - Design and coding required

Number of Pages Required

5+ page

Font styles to use
Sans Serif

Colors

Designer to choose colors to be used in the design.

Requirements
Must have
• KVR GLOBALINKS
• KVR globalinks Trading & Contracting provides various services. The Company offers infrastructure construction, oil, enegy and gas services, agricultural projects, real estate development, travel and tourism, and food processing and trading.
• Civil contracting for infrastructure, residential and heavy projects. Through its main subsidiaries; distribution of general food products, construction chemicals including corrosion inhibitors and electrical machinery; provides catering and travel agency services; ownership and operation of a school; offers human sources services including manpower supply.
• Drilling and Gold Mines Used Machinery, All Kinds of Construction Machinery, Drilling Machines are manufactured and sold.
Nice to have
• good designa and beautiful colours, it has too look professional

```html
<!DOCTYPE html>
<html lang="en">
<head>
<meta charset="utf-8">
<title>KVR Globalinks – Website Concepts</title>
<link href="https://fonts.googleapis.com/css2?family=Poppins:wght@300;400;500;600;700&display=swap" rel="stylesheet">
<style>
:root{
  --board:#232323;
  --red:#a8121e;
  --red-bright:#c8202c;
  --black:#0d0d0d;
  --ink:#151515;
  --dark:#1a1a1a;
  --white:#ffffff;
  --muted:#8a8a8a;
  --text:#555555;
  --line:#3a3a3a;
}
*{margin:0;padding:0;box-sizing:border-box}
html,body{width:758px;height:1200px;overflow:hidden;background:var(--board);font-family:'Poppins',sans-serif}
.ab{position:absolute}
.panel{position:absolute;overflow:hidden}
.light-site{left:21px;top:22px;width:355px;height:1150px;background:var(--white)}
.dark-site{left:392px;top:23px;width:351px;height:1102px;background:var(--black)}
.brand{font-weight:600;color:var(--white);letter-spacing:.08em;white-space:nowrap}
.nav{font-size:4.6px;color:var(--white);white-space:nowrap}
.nav.active{color:var(--red-bright);text-decoration:underline}
.photo{position:absolute}
.btn{position:absolute;background:var(--red);color:var(--white);font-weight:600;display:flex;align-items:center;justify-content:center;white-space:nowrap}
.pill{border-radius:8px;background:var(--red-bright)}
.h-red{color:var(--red);font-weight:700;white-space:nowrap}
.h-white{color:var(--white);font-weight:700;white-space:nowrap}
.body-copy{font-size:4.1px;line-height:7.6px;color:var(--text)}
.svc-title{font-size:4.6px;font-weight:600;color:var(--red);white-space:nowrap}
.arrow-tab{position:absolute;width:12px;height:10px;background:var(--white);display:flex;align-items:center;justify-content:center}
.foot-link{font-size:4.3px;color:#ddd;line-height:7.5px}
.center{text-align:center}
.tile-label{position:absolute;color:var(--white);font-size:4.4px;font-weight:600;text-align:center;line-height:7.5px}
.field{position:absolute;background:var(--white);border:1px solid #ccc;font-size:4px;color:#999;padding:3px 2px}
</style>
</head>
<body>

<!-- ============ LIGHT CONCEPT ============ -->
<section class="panel light-site">
  <!-- header -->
  <div class="ab" style="left:0;top:0;width:355px;height:26px;background:var(--black)"></div>
  <div class="ab brand" style="left:22px;top:10px;font-size:4.6px">KVR GLOBALINKS</div>
  <div class="ab nav active" style="left:108px;top:10px">Home</div>
  <div class="ab nav" style="left:133px;top:10px">About Us</div>
  <div class="ab nav" style="left:164px;top:10px">Services</div>
  <div class="ab nav" style="left:195px;top:10px">Blog</div>
  <div class="ab nav" style="left:216px;top:10px">Contact Us</div>
  <svg class="ab" style="left:253px;top:11px" width="5" height="5" viewBox="0 0 10 10"><circle cx="4" cy="4" r="3" fill="none" stroke="#fff" stroke-width="1.6"/><line x1="6.3" y1="6.3" x2="9" y2="9" stroke="#fff" stroke-width="1.6"/></svg>
  <div class="ab" style="left:267px;top:10px;width:6px;height:6px;background:var(--red);border-radius:1px"></div>
  <div class="ab nav" style="left:275px;top:9.5px;font-size:5.4px">: +1 888 888 8888</div>

  <!-- hero -->
  <div class="photo" role="img" aria-label="Cargo ship at a container port with cranes and an aeroplane overhead" style="left:0;top:26px;width:355px;height:166px;background:linear-gradient(160deg,#6f8fb8 0%,#a9bcd2 35%,#c9a27a 55%,#3b79b5 70%,#7b3a2c 100%)"></div>
  <div class="ab" style="left:33px;top:74px;font-size:11px;color:#fff;font-weight:300;white-space:nowrap">WELCOME TO</div>
  <div class="ab h-white" style="left:33px;top:86px;font-size:14px">KVR GLOBALINKS</div>
  <div class="ab" style="left:33px;top:106px;width:150px;font-size:4.6px;line-height:7.4px;color:#f3f3f3">Lorem ipsum dolor sit amet, consectetur adipiscing elit, sed do eiusmod tempor incididunt ut labore et</div>
  <div class="btn" style="left:33px;top:126px;width:33px;height:13px;font-size:4.4px">GET STARTED</div>
  <div class="ab" style="left:339px;top:86px;width:2px;height:2px;border-radius:50%;background:var(--red)"></div>
  <div class="ab" style="left:339px;top:90.5px;width:2px;height:2px;border-radius:50%;background:#bbb"></div>
  <div class="ab" style="left:339px;top:95px;width:2px;height:2px;border-radius:50%;background:#bbb"></div>
  <div class="ab" style="left:339px;top:99.5px;width:2px;height:2px;border-radius:50%;background:#bbb"></div>

  <!-- about -->
  <div class="ab h-red center" style="left:0;top:216px;width:353px;font-size:11px">ABOUT US</div>
  <div class="ab" style="left:40px;top:239px;width:148px;height:92px;background:var(--black);display:flex;align-items:center;justify-content:center">
    <span class="brand" style="font-size:8px;font-weight:400;letter-spacing:.12em">KVR GLOBALINKS</span>
  </div>
  <div class="ab" style="left:177px;top:245px;width:137px;height:81px;border:1px solid var(--red);background:var(--white)"></div>
  <div class="ab body-copy" style="left:184px;top:250px;width:123px;text-align:justify">Lorem ipsum dolor sit amet, consectetur adipiscing elit, sed do eiusmod tempor incididunt ut labore et dolore magna aliqua. Ut enim ad minim veniam, quis nostrud exercitation ullamco laboris nisi ut aliquip ex ea commodo consequat. Duis aute irure dolor in reprehe nderit in voluptate velit esse cillum dolore eu fugiat nulla pariatur</div>
  <div class="btn" style="left:184px;top:306px;width:40px;height:14px;font-size:4.4px">READ MORE ›</div>

  <!-- services band -->
  <div class="ab" style="left:0;top:356px;width:355px;height:49px;background:var(--red)"></div>
  <div class="ab h-white" style="left:46px;top:373px;font-size:11px">OUR SERVICES</div>
  <div class="ab" style="left:55px;top:387px;font-size:3.9px;color:#f1d3d5;letter-spacing:.1em;white-space:nowrap">Trading &amp; Contracting</div>
  <div class="ab" style="left:139px;top:375px;width:180px;font-size:4.3px;line-height:7.6px;color:#f5e1e2">Lorem ipsum dolor sit amet, consectetur adipiscing elit, sed do eiusmod tempor incididunt ut labore et dolore magna aliqua. Ut enim ad minim veniam,</div>

  <!-- services grid -->
  <div class="photo" role="img" aria-label="Aerial view of a large infrastructure construction site" style="left:35px;top:414px;width:91px;height:71px;background:linear-gradient(150deg,#8d97a2,#c3c8cc 50%,#6d7b5e)"></div>
  <div class="arrow-tab" style="left:114px;top:475px"><svg width="6" height="4" viewBox="0 0 12 8"><path d="M0 4H10M7 1L10 4L7 7" stroke="#111" stroke-width="1.4" fill="none"/></svg></div>
  <div class="ab svc-title" style="left:35px;top:489px">INFRASTRUCTURE CONSTRUCTION</div>
  <div class="ab body-copy" style="left:35px;top:498px;width:92px">Lorem ipsum dolor sit amet, consectetur adipiscing elit, sed do eiusmod tempor incididunt ut labore et dolore magna</div>

  <div class="photo" role="img" aria-label="Offshore oil rig at sea seen from above" style="left:130px;top:414px;width:92px;height:71px;background:linear-gradient(160deg,#465c62,#2b3c40 60%,#8b5a2f)"></div>
  <div class="arrow-tab" style="left:210px;top:475px"><svg width="6" height="4" viewBox="0 0 12 8"><path d="M0 4H10M7 1L10 4L7 7" stroke="#111" stroke-width="1.4" fill="none"/></svg></div>
  <div class="ab svc-title" style="left:130px;top:489px">OIL, ENERGY AND GAS SERVICES</div>
  <div class="ab body-copy" style="left:130px;top:498px;width:92px">Lorem ipsum dolor sit amet, consectetur adipiscing elit, sed do eiusmod tempor incididunt ut labore et dolore magna</div>

  <div class="photo" role="img" aria-label="Greenhouse with a tablet showing crop data" style="left:226px;top:414px;width:91px;height:71px;background:linear-gradient(150deg,#dfe6ea,#b7c3bf 50%,#6f8a4f)"></div>
  <div class="arrow-tab" style="left:305px;top:475px"><svg width="6" height="4" viewBox="0 0 12 8"><path d="M0 4H10M7 1L10 4L7 7" stroke="#111" stroke-width="1.4" fill="none"/></svg></div>
  <div class="ab svc-title" style="left:226px;top:489px">AGRICULTURAL PROJECTS</div>
  <div class="ab body-copy" style="left:226px;top:498px;width:92px">Lorem ipsum dolor sit amet, consectetur adipiscing elit, sed do eiusmod tempor incididunt ut labore et dolore magna</div>

  <div class="photo" role="img" aria-label="Tower cranes over residential buildings under construction" style="left:34px;top:528px;width:91px;height:71px;background:linear-gradient(180deg,#9ab3cf,#c7d3df 45%,#2f3d57)"></div>
  <div class="arrow-tab" style="left:113px;top:589px"><svg width="6" height="4" viewBox="0 0 12 8"><path d="M0 4H10M7 1L10 4L7 7" stroke="#111" stroke-width="1.4" fill="none"/></svg></div>
  <div class="ab svc-title" style="left:34px;top:603px">REAL ESTATE DEVELOPMENT</div>
  <div class="ab body-copy" style="left:34px;top:612px;width:92px">Lorem ipsum dolor sit amet, consectetur adipiscing elit, sed do eiusmod tempor incididunt ut labore et dolore magna</div>

  <div class="photo" role="img" aria-label="World landmarks rising from clouds on an open hand" style="left:131px;top:528px;width:91px;height:71px;background:linear-gradient(180deg,#f1f1f1,#d8dde2 55%,#a79f96)"></div>
  <div class="arrow-tab" style="left:210px;top:589px"><svg width="6" height="4" viewBox="0 0 12 8"><path d="M0 4H10M7 1L10 4L7 7" stroke="#111" stroke-width="1.4" fill="none"/></svg></div>
  <div class="ab svc-title" style="left:131px;top:603px">TRAVEL AND TOURISM</div>
  <div class="ab body-copy" style="left:131px;top:612px;width:92px">Lorem ipsum dolor sit amet, consectetur adipiscing elit, sed do eiusmod tempor incididunt ut labore et dolore magna</div>

  <div class="photo" role="img" aria-label="Assorted fresh vegetables, cheese, bread and bottled goods" style="left:227px;top:528px;width:91px;height:71px;background:linear-gradient(150deg,#c23a1e,#d7a043 45%,#5f8a2e 75%,#f2e6cf)"></div>
  <div class="arrow-tab" style="left:306px;top:589px"><svg width="6" height="4" viewBox="0 0 12 8"><path d="M0 4H10M7 1L10 4L7 7" stroke="#111" stroke-width="1.4" fill="none"/></svg></div>
  <div class="ab svc-title" style="left:227px;top:603px">FOOD PROCESSING</div>
  <div class="ab body-copy" style="left:227px;top:612px;width:92px">Lorem ipsum dolor sit amet, consectetur adipiscing elit, sed do eiusmod tempor incididunt ut labore et dolore magna</div>

  <div class="ab" style="left:174px;top:645px;width:3px;height:3px;border-radius:50%;background:var(--red)"></div>
  <div class="ab" style="left:178.5px;top:645px;width:3px;height:3px;border-radius:50%;background:#999"></div>

  <!-- testimonial band -->
  <div class="photo" role="img" aria-label="Darkened container port backdrop" style="left:0;top:675px;width:355px;height:121px;background:linear-gradient(90deg,#1b1b1b,#2c2c2c 50%,#161616)"></div>
  <div class="ab" style="left:47px;top:703px;font-size:11px;color:#fff;font-weight:400;white-space:nowrap">WHAT OUR</div>
  <div class="ab h-white" style="left:47px;top:715px;font-size:15px">CLEINTS SAY</div>
  <div class="ab" style="left:50px;top:738px;font-size:3.9px;color:#ccc;white-space:nowrap">READ ALL TESTIMONIAL</div>
  <div class="ab" style="left:97px;top:736px;width:10px;height:7px;background:var(--red)"></div>
  <div class="ab" style="left:177px;top:713px;width:145px;height:116px;background:var(--red);box-shadow:0 2px 4px rgba(0,0,0,.25)"></div>
  <div class="ab" style="left:179px;top:709px;font-size:17px;color:#f4c7c9;font-weight:700;line-height:1">“</div>
  <div class="ab" style="left:196px;top:730px;width:115px;font-size:5px;line-height:7.6px;color:#fff">Lorem ipsum dolor sit amet, consectetur adipi scing elit, sed do eiusmod tempor incididunt ut labore et dolore magna aliqua. Ut enim ad min im veniam, quis nostrud</div>
  <div class="photo" role="img" aria-label="Client portrait" style="left:196px;top:772px;width:15px;height:15px;border-radius:50%;background:linear-gradient(160deg,#c9b6a3,#5a4a40)"></div>
  <div class="ab" style="left:224px;top:772px;font-size:5px;color:#fff;font-weight:600;white-space:nowrap">JOHN DOE</div>
  <div class="ab" style="left:224px;top:779px;font-size:5.5px;color:#f3b51b;letter-spacing:.5px;white-space:nowrap">★★★★★</div>
  <div class="ab" style="left:236px;top:808px;display:flex;gap:1.3px">
    <span style="width:3px;height:3px;border-radius:50%;background:#fff"></span><span style="width:3px;height:3px;border-radius:50%;background:#8b8b8b"></span><span style="width:3px;height:3px;border-radius:50%;background:#8b8b8b"></span><span style="width:3px;height:3px;border-radius:50%;background:#8b8b8b"></span><span style="width:3px;height:3px;border-radius:50%;background:#8b8b8b"></span>
  </div>
  <div class="ab" style="left:308px;top:813px;font-size:17px;color:#f4c7c9;font-weight:700;line-height:1">”</div>

  <!-- blog -->
  <div class="ab h-red center" style="left:0;top:852px;width:355px;font-size:11px">ORU BLOG POST</div>
  <div class="photo" role="img" aria-label="Engineer in hard hat and safety vest at a container yard" style="left:32px;top:878px;width:142px;height:76px;background:linear-gradient(150deg,#7e96b3,#2f4569 55%,#8a3a2a)"></div>
  <div class="photo" role="img" aria-label="Trucks and containers at sunset with an aeroplane overhead" style="left:179px;top:878px;width:142px;height:76px;background:linear-gradient(170deg,#7c8fa6,#e29a4a 55%,#37302c)"></div>
  <div class="ab" style="left:27px;top:907px;width:11px;height:11px;border-radius:50%;background:#555;display:flex;align-items:center;justify-content:center;color:#fff;font-size:6px">‹</div>
  <div class="ab" style="left:315px;top:907px;width:11px;height:11px;border-radius:50%;background:#555;display:flex;align-items:center;justify-content:center;color:#fff;font-size:6px">›</div>

  <div class="ab" style="left:36px;top:945px;width:51px;height:42px;background:#fff;box-shadow:0 1px 3px rgba(0,0,0,.25)"></div>
  <div class="ab" style="left:43px;top:950px;font-size:4.8px;line-height:10px;color:#555;white-space:nowrap"><span style="color:var(--red)">▪</span> 14-01-2020<br><span style="color:var(--red)">●</span> By John Doe<br><span style="color:var(--red)">●</span> Comment(10)</div>
  <div class="ab" style="left:89px;top:961px;width:86px;font-size:4.1px;line-height:7.5px;color:var(--red)">Lorem ipsum dolor sit amet, consectetur a dipiscing elit, sed do eiusmod tempor incid<br>Continue Reading</div>

  <div class="ab" style="left:183px;top:945px;width:51px;height:42px;background:#fff;box-shadow:0 1px 3px rgba(0,0,0,.25)"></div>
  <div class="ab" style="left:190px;top:950px;font-size:4.8px;line-height:10px;color:#555;white-space:nowrap"><span style="color:var(--red)">▪</span> 14-01-2020<br><span style="color:var(--red)">●</span> By John Doe<br><span style="color:var(--red)">●</span> Comment(10)</div>
  <div class="ab" style="left:236px;top:961px;width:86px;font-size:4.1px;line-height:7.5px;color:#666">Lorem ipsum dolor sit amet, consectetur adipiscing elit, sed do eiusmod tempor i<br>Continue Reading</div>

  <!-- footer -->
  <div class="ab" style="left:0;top:1038px;width:355px;height:112px;background:var(--ink)"></div>
  <div class="btn" style="left:37px;top:1022px;width:71px;height:28px;flex-direction:column;font-weight:400">
    <span style="font-size:4.8px;font-weight:600;display:flex;align-items:center;gap:2px"><svg width="8" height="8" viewBox="0 0 16 16"><circle cx="8" cy="8" r="7" stroke="#fff" fill="none"/><path d="M8 4a2.5 2.5 0 0 1 2.5 2.5C10.5 8.5 8 12 8 12S5.5 8.5 5.5 6.5A2.5 2.5 0 0 1 8 4z" fill="#fff"/></svg>ADDRESS</span>
    <span style="font-size:4.3px;line-height:5px;text-align:center">Lorem ipsum dolor sit<br>amet</span>
  </div>
  <div class="btn" style="left:143px;top:1022px;width:71px;height:28px;flex-direction:column;font-weight:400">
    <span style="font-size:4.8px;font-weight:600;display:flex;align-items:center;gap:2px"><svg width="8" height="8" viewBox="0 0 16 16"><circle cx="8" cy="8" r="7" stroke="#fff" fill="none"/><path d="M5.5 4.5l1.5-.5 1 2-1 1a5 5 0 0 0 2 2l1-1 2 1-.5 1.5c-3 .5-6.5-3-6-6z" fill="#fff"/></svg>PHONE</span>
    <span style="font-size:4.3px;margin-top:2px">+ 1 888 888 8888</span>
  </div>
  <div class="btn" style="left:248px;top:1022px;width:71px;height:28px;flex-direction:column;font-weight:400">
    <span style="font-size:4.8px;font-weight:600;display:flex;align-items:center;gap:2px"><svg width="8" height="8" viewBox="0 0 16 16"><circle cx="8" cy="8" r="7" stroke="#fff" fill="none"/><rect x="4" y="5.5" width="8" height="5.5" fill="#fff"/><path d="M4 5.5l4 3 4-3" stroke="#a8121e" fill="none" stroke-width=".8"/></svg>EMAIL ADDRESS</span>
    <span style="font-size:4.3px;margin-top:2px">info@kvrglobalinks.com</span>
  </div>
  <div class="ab brand" style="left:44px;top:1084px;font-size:4.8px">KVR GLOBALINKS</div>
  <div class="ab" style="left:38px;top:1095px;width:82px;font-size:4.3px;line-height:7.5px;color:#ddd">Lorem ipsum dolor sit amet, consec tetur adipiscing elit, sed do eiusmod tempor incididunt</div>
  <div class="ab" style="left:171px;top:1060px;font-size:4.8px;color:#fff;font-weight:600">QUICK LINKS</div>
  <div class="ab foot-link" style="left:173px;top:1071px">Home<br>About US<br>Services<br>Blog<br>Contact us</div>
  <div class="ab" style="left:255px;top:1060px;font-size:4.8px;color:#fff;font-weight:600">NEWSLETTERS</div>
  <div class="field" style="left:255px;top:1069px;width:66px;height:10px;font-size:4.3px;padding:2px 2px;color:#888">Enter the Email</div>
  <div class="btn" style="left:255px;top:1087px;width:34px;height:12px;font-size:4.3px">SUBSCRIBE</div>
  <div class="ab" style="left:255px;top:1110px;display:flex;gap:3px">
    <span style="width:4px;height:4px;border-radius:50%;background:var(--red)"></span><span style="width:4px;height:4px;border-radius:50%;background:var(--red)"></span><span style="width:4px;height:4px;border-radius:50%;background:var(--red)"></span><span style="width:4px;height:4px;border-radius:50%;background:var(--red)"></span>
  </div>
  <div class="ab center" style="left:0;top:1132px;width:355px;font-size:3.8px;color:#ddd">© Copyrights@ 2020 KVR Globalinks &nbsp;|&nbsp; All Rights Reserved</div>
</section>

<!-- ============ DARK CONCEPT ============ -->
<section class="panel dark-site">
  <!-- header -->
  <div class="ab" style="left:0;top:0;width:351px;height:33px;background:var(--black)"></div>
  <div class="ab" style="left:101px;top:4px;width:8px;height:8px;border:1px solid #fff;border-radius:50%;display:flex;align-items:center;justify-content:center"><svg width="4" height="4" viewBox="0 0 10 10"><path d="M1.5 1.5l2-.5 1 2.5-1 1a5 5 0 0 0 2 2l1-1 2.5 1-.5 2C4 9 1 6 1.5 1.5z" fill="#fff"/></svg></div>
  <div class="ab nav" style="left:112px;top:5.5px;font-size:4.2px">+ 1 888 888 8888</div>
  <div class="ab" style="left:251px;top:4px;width:8px;height:8px;border:1px solid #fff;border-radius:50%;display:flex;align-items:center;justify-content:center"><svg width="4" height="3" viewBox="0 0 10 7"><rect width="10" height="7" fill="#fff"/><path d="M0 0l5 4 5-4" stroke="#000" fill="none"/></svg></div>
  <div class="ab nav" style="left:262px;top:5.5px;font-size:4.2px">info@kvrglobalinks.com</div>
  <div class="ab brand" style="left:34px;top:17px;font-size:5px">KVR GLOBALINKS</div>
  <div class="btn" style="left:152px;top:18px;width:23px;height:10px;font-size:4.6px;font-weight:400;background:var(--red-bright)">Home</div>
  <div class="ab nav" style="left:183px;top:20.5px">About Us</div>
  <div class="ab nav" style="left:217px;top:20.5px">Services</div>
  <div class="ab nav" style="left:250px;top:20.5px">Blog</div>
  <div class="ab nav" style="left:274px;top:20.5px">Contact Us</div>
  <svg class="ab" style="left:314px;top:21px" width="5" height="5" viewBox="0 0 10 10"><circle cx="4" cy="4" r="3" fill="none" stroke="#fff" stroke-width="1.6"/><line x1="6.3" y1="6.3" x2="9" y2="9" stroke="#fff" stroke-width="1.6"/></svg>

  <!-- hero -->
  <div class="photo" role="img" aria-label="Container terminal with trucks at sunset and an aeroplane in the sky" style="left:0;top:33px;width:351px;height:166px;background:linear-gradient(180deg,#4b5a6e 0%,#b98a63 35%,#f0a443 55%,#7a3b1f 80%,#2a2a2e 100%)"></div>
  <div class="ab h-white center" style="left:0;top:74px;width:351px;font-size:14.5px">KVR GLOBALINKS</div>
  <div class="ab center" style="left:95px;top:96px;width:161px;font-size:4.6px;line-height:7.5px;color:#f6e4d0">Lorem ipsum dolor sit amet, consectetur adipiscing elit, sed do eiusmod tempor incididunt ut labore et</div>
  <div class="btn pill" style="left:153px;top:115px;width:45px;height:13px;font-size:4.4px">GET STARTED</div>

  <!-- about -->
  <div class="photo" role="img" aria-label="Faded industrial port skyline" style="left:0;top:199px;width:351px;height:121px;background:linear-gradient(180deg,#111 0%,#1c1c1c 60%,#2b2b2b 100%)"></div>
  <div class="ab h-white center" style="left:0;top:224px;width:351px;font-size:11px">ABOUT US</div>
  <div class="ab center" style="left:0;top:239px;width:351px;font-size:11px;color:#fff;font-weight:300">KVR GLOBALINKS</div>
  <div class="ab center" style="left:57px;top:258px;width:237px;font-size:4.3px;line-height:7.6px;color:#ddd">Lorem ipsum dolor sit amet, consectetur adipiscing elit, sed do eiusmod tempor incididunt ut labore et dolore magna aliqua. Ut enim ad minim veniam, quis nostrud exercitation ullamco laboris nisi ut aliquip ex ea commodo consequat. Duis aute irure dolor in reprehenderit in voluptate velit esse cillum dolore eu fugiat nulla pariatur. Excepteur sint occaecat cupidatat non proident, sunt in culpa qui</div>
  <div class="btn pill" style="left:153px;top:293px;width:45px;height:14px;font-size:4.4px">LEARN MORE</div>

  <!-- services -->
  <div class="ab h-white center" style="left:0;top:332px;width:351px;font-size:11px">OUR SERVICES</div>
  <div class="ab center" style="left:0;top:349px;width:351px;font-size:4.3px;color:#ddd">Lorem ipsum dolor sit amet, consectetur adipiscing elit, sed do eiusmod</div>
  <div class="photo" role="img" aria-label="Aerial view of an infrastructure construction site" style="left:32.5px;top:370.5px;width:85px;height:61px;background:linear-gradient(150deg,#56606a,#8b9298 60%,#3f4a3d)"></div>
  <div class="tile-label" style="left:32.5px;top:396px;width:85px">INFRASTRUCTURE<br>CONSTRUCTION</div>
  <div class="photo" role="img" aria-label="Offshore oil rig at sea" style="left:120px;top:370.5px;width:85px;height:61px;background:linear-gradient(160deg,#3e4f55,#1f2b2f 60%,#6a4524)"></div>
  <div class="tile-label" style="left:120px;top:396px;width:85px">OIL, ENERGY AND<br>GAS SERVICES</div>
  <div class="photo" role="img" aria-label="Tower cranes over buildings under construction" style="left:32.5px;top:433px;width:85px;height:60px;background:linear-gradient(180deg,#5f7590,#3a4a5e 60%,#2a2a2a)"></div>
  <div class="tile-label" style="left:32.5px;top:458px;width:85px">REAL ESTATE<br>DEVELOPMENT</div>
  <div class="photo" role="img" aria-label="Greenhouse with a tablet showing crop data" style="left:120px;top:433px;width:85px;height:60px;background:linear-gradient(150deg,#7b8581,#5a6658 60%,#3c4732)"></div>
  <div class="tile-label" style="left:120px;top:458px;width:85px">AGRICULTURAL<br>PROJECTS</div>
  <div class="photo" role="img" aria-label="Travel world map with hat and sunglasses on a wooden table" style="left:207.5px;top:370.5px;width:111px;height:122.5px;background:linear-gradient(150deg,#b9a88c,#8d7a62 50%,#3b3631)"></div>
  <div class="tile-label" style="left:207.5px;top:470px;width:111px">TRAVEL AND TOURISM</div>
  <div class="ab" style="left:285px;top:499px;font-size:3.9px;color:var(--red-bright);white-space:nowrap">more services »</div>

  <!-- testimonials -->
  <div class="photo" role="img" aria-label="Red-tinted port scene with aeroplane and containers" style="left:0;top:528px;width:351px;height:166px;background:linear-gradient(160deg,#8f141d,#c4202b 45%,#a9141f 100%)"></div>
  <div class="ab h-white center" style="left:0;top:552px;width:351px;font-size:11px">WHAT OUR CLEINTS SAY</div>
  <div class="photo" role="img" aria-label="Client portrait" style="left:8.5px;top:589.5px;width:16px;height:16px;border-radius:50%;border:1px solid #fff;background:linear-gradient(160deg,#e0c2a8,#8a5a40)"></div>
  <div class="photo" role="img" aria-label="Client portrait" style="left:284px;top:558px;width:16px;height:16px;border-radius:50%;border:1px solid #fff;background:linear-gradient(160deg,#e0c2a8,#6a4a3a)"></div>
  <div class="photo" role="img" aria-label="Client portrait" style="left:23.5px;top:652.5px;width:16px;height:16px;border-radius:50%;border:1px solid #fff;background:linear-gradient(160deg,#d8c0aa,#4a3a30)"></div>
  <div class="photo" role="img" aria-label="Client portrait" style="left:319.5px;top:647.5px;width:16px;height:16px;border-radius:50%;border:1px solid #fff;background:linear-gradient(160deg,#e6c9ae,#7a5a45)"></div>
  <div class="ab" style="left:31px;top:601px;font-size:8px;color:#fff">‹</div>
  <div class="ab" style="left:316px;top:601px;font-size:8px;color:#fff">›</div>

  <div class="ab" style="left:51px;top:592px;font-size:8px;color:#fff;font-weight:700;line-height:1">“</div>
  <div class="photo" role="img" aria-label="Client portrait" style="left:51px;top:596px;width:24px;height:24px;border-radius:50%;background:linear-gradient(160deg,#e3c7ad,#7b4e35)"></div>
  <div class="ab" style="left:82.5px;top:595px;width:88px;font-size:4.3px;line-height:6.6px;color:#fff;text-align:justify">Lorem ipsum dolor sit amet, consectetur adipiscing elit, sed do eiusmod tempor incididunt ut labore et dolore magna aliqua. Ut enim ad</div>
  <div class="ab" style="left:84px;top:623px;font-size:4.8px;color:#fff;font-weight:500;white-space:nowrap">JOHN DOE</div>

  <div class="ab" style="left:177px;top:592px;font-size:8px;color:#fff;font-weight:700;line-height:1">“</div>
  <div class="photo" role="img" aria-label="Client portrait" style="left:177px;top:596px;width:24px;height:24px;border-radius:50%;background:linear-gradient(160deg,#e1c4a8,#4d6a8a)"></div>
  <div class="ab" style="left:208.5px;top:595px;width:88px;font-size:4.3px;line-height:6.6px;color:#fff;text-align:justify">Lorem ipsum dolor sit amet, consectetur adipiscing elit, sed do eiusmod tempor incididunt ut labore et dolore magna aliqua. Ut enim ad</div>
  <div class="ab" style="left:210px;top:623px;font-size:4.8px;color:#fff;font-weight:500;white-space:nowrap">JOHN DOE</div>

  <!-- latest news -->
  <div class="ab center" style="left:0;top:713px;width:351px;font-size:11px;font-weight:600;color:#fff">LASTEST <span style="color:var(--red-bright)">NEWS</span></div>
  <div class="photo" role="img" aria-label="Business handshake over a container port at dawn" style="left:32px;top:734.5px;width:152.5px;height:91px;background:linear-gradient(150deg,#6a8aae,#a9b9c8 45%,#2c4868)"></div>
  <div class="ab" style="left:32px;top:825.5px;width:152.5px;height:80.5px;background:#111"></div>
  <div class="ab" style="left:45px;top:830px;font-size:5.3px;color:var(--red-bright);white-space:nowrap">Lorem ipsum dolor sit amet, consectetur</div>
  <div class="ab" style="left:45px;top:843px;width:100px;font-size:3.9px;line-height:7.6px;color:#ddd">Lorem ipsum dolor sit amet, consectetur adipiscing elit, sed do eiusmod tempor incididunt ut labore et dolore magna aliqua.</div>
  <div class="btn pill" style="left:43px;top:875.5px;width:40px;height:14px;font-size:4.4px">READ MORE »</div>

  <div class="ab" style="left:185.5px;top:734.5px;width:132px;height:171.5px;background:#111"></div>
  <div class="photo" role="img" aria-label="Engineer in hard hat at a container yard" style="left:185.5px;top:734.5px;width:57px;height:56px;background:linear-gradient(150deg,#4a6aa0,#c8c23a 60%,#7a2a2a)"></div>
  <div class="ab" style="left:248px;top:740px;font-size:5.3px;color:var(--red-bright);white-space:nowrap">Lorem ipsum dolor sit</div>
  <div class="ab" style="left:248px;top:749px;width:66px;font-size:3.9px;line-height:7.8px;color:#ddd">Lorem ipsum dolor sit amet, consectetur adipiscing elit</div>
  <div class="btn pill" style="left:253.5px;top:771px;width:44px;height:13px;font-size:4.4px">READ MORE »</div>

  <div class="photo" role="img" aria-label="Assorted fresh vegetables and packaged food" style="left:185.5px;top:792.5px;width:57px;height:55.5px;background:linear-gradient(150deg,#c23a1e,#d7a043 45%,#5f8a2e 75%,#f2e6cf)"></div>
  <div class="ab" style="left:248px;top:798px;font-size:5.3px;color:var(--red-bright);white-space:nowrap">Lorem ipsum dolor sit</div>
  <div class="ab" style="left:248px;top:807px;width:66px;font-size:3.9px;line-height:7.8px;color:#ddd">Lorem ipsum dolor sit amet, consectetur adipiscing elit</div>
  <div class="btn pill" style="left:253.5px;top:829px;width:44px;height:13px;font-size:4.4px">READ MORE »</div>

  <div class="photo" role="img" aria-label="Warehouse worker scanning boxes with a tablet" style="left:185.5px;top:850px;width:57px;height:56px;background:linear-gradient(150deg,#e8e2d8,#c6a77e 55%,#8a6a48)"></div>
  <div class="ab" style="left:248px;top:856px;font-size:5.3px;color:var(--red-bright);white-space:nowrap">Lorem ipsum dolor sit</div>
  <div class="ab" style="left:248px;top:865px;width:66px;font-size:3.9px;line-height:7.8px;color:#ddd">Lorem ipsum dolor sit amet, consectetur adipiscing elit</div>
  <div class="btn pill" style="left:253.5px;top:886px;width:44px;height:13px;font-size:4.4px">READ MORE »</div>

  <!-- footer -->
  <div class="ab" style="left:0;top:932px;width:351px;height:148px;background:#050505"></div>
  <div class="ab" style="left:46.5px;top:951.5px;font-size:5.2px;font-weight:600;color:#fff;white-space:nowrap">Subscribe our Newsletter Now !</div>
  <div class="field" style="left:172px;top:947px;width:83px;height:15px;background:#111;border-color:#777;font-size:3.8px;padding:5px 2px;color:#bbb">Enter the Email</div>
  <div class="btn pill" style="left:267.5px;top:949px;width:31.5px;height:11px;font-size:4.2px">SUBCRIBE</div>
  <div class="ab" style="left:32px;top:970px;width:286px;height:1px;background:var(--line)"></div>

  <div class="ab" style="left:40px;top:978px;font-size:6px;font-weight:600;color:#fff;white-space:nowrap">Get In Touch</div>
  <div class="field" style="left:39.5px;top:990.5px;width:51.5px;height:11.5px">First Name</div>
  <div class="field" style="left:93.5px;top:990.5px;width:52px;height:11.5px">Last Name</div>
  <div class="field" style="left:39.5px;top:1005.5px;width:51.5px;height:11.5px">Email</div>
  <div class="field" style="left:93.5px;top:1005.5px;width:52px;height:11.5px">Phone</div>
  <div class="field" style="left:39.5px;top:1020.5px;width:106px;height:24.5px">Message</div>
  <div class="btn pill" style="left:41.5px;top:1052px;width:32px;height:10.5px;font-size:4.3px">SUBMIT</div>
  <div class="ab" style="left:42px;top:1070px;display:flex;gap:5px">
    <span style="width:4px;height:4px;background:var(--red-bright)"></span><span style="width:4px;height:4px;border-radius:50%;background:var(--red-bright)"></span><span style="width:4px;height:4px;background:var(--red-bright)"></span><span style="width:4px;height:4px;border-radius:50%;background:var(--red-bright)"></span>
  </div>

  <div class="ab" style="left:168px;top:978px;font-size:6px;font-weight:600;color:#fff;white-space:nowrap">Quick Links</div>
  <div class="ab foot-link" style="left:171px;top:992px">Home<br>About Us<br>Services<br>Blog<br>Contact Us</div>

  <div class="ab" style="left:249px;top:978px;font-size:6px;font-weight:600;color:#fff;white-space:nowrap">Contact Us</div>
  <div class="ab" style="left:249px;top:990px;font-size:4.3px;color:var(--red-bright)">●</div>
  <div class="ab foot-link" style="left:254px;top:989.5px">Lorem ipsum dolor sit<br>amet, consectetur</div>
  <div class="ab" style="left:246px;top:1013px;width:4px;height:3px;background:var(--red-bright)"></div>
  <div class="ab foot-link" style="left:253px;top:1011px">info@kvrglobalinks.com</div>
  <div class="ab" style="left:246px;top:1028px;font-size:4px;color:var(--red-bright)">✆</div>
  <div class="ab foot-link" style="left:252px;top:1026px">+1 888 888 8888</div>

  <div class="ab" style="left:0;top:1080px;width:351px;height:22px;background:var(--dark)"></div>
  <div class="ab center" style="left:0;top:1089px;width:351px;font-size:3.8px;color:#ddd">© Copyrights@ 2020 KVR Globalinks &nbsp;|&nbsp; All Rights Reserved</div>
</section>

</body>
</html>
```